Refresh Brightpath Coursecraft

Need a new design for e-learning development and web app development site: http://brightpathcoursecraft.example. Need pages for everything on menu bar plus a training services and a web app development services pages and a better page for samples http://brightpathcoursecraft.example/samples5/.

***Must be programmed in html 5. NO CMS. No WP. No Plume. Straight html/css.

Target Market(s)

government

Industry/Entity Type

Government

Coding

Coded - Design and coding required

Number of Pages Required

1 page

Requirements
Must have
• Must be coded in html5/css. No CMS.
• Divided so you can easily see that we offer 3 separate services:
• Live Training - E-Learning Development - Web App Development
• A way to display logos of all our clients like on bottom of this page: https://www.quorvatests.example (this is also our website so you can copy all these logos)
• List both our Denver location which is already on our website plus our office in Velmoro Plaza. Street 62 Sur, 14-87. Medellín, Antioquia.
• A page like this for our web app dev services https://www.tekvanu.example/product-development
Should not have
• CMS

```html
<!DOCTYPE html>
<html lang="en">
<head>
<meta charset="utf-8">
<title>Brightpath Coursecraft</title>
<link href="https://fonts.googleapis.com/css2?family=Montserrat:wght@400;500;600;700&family=Open+Sans:wght@400;600;700&display=swap" rel="stylesheet">
<style>
:root{
  --orange:#f39a1e;
  --orange-deep:#e8871a;
  --blue:#1f6fb5;
  --ink:#1c1c1c;
  --text:#555;
  --footer:#1e1e1e;
}
*{margin:0;padding:0;box-sizing:border-box}
html,body{width:1200px;height:4036px;overflow:hidden;background:#fff}
body{position:relative;font-family:"Open Sans",Arial,sans-serif;color:var(--text)}
.abs{position:absolute}
.site-header{left:0;top:0;width:1200px;height:118px;background:#fff;border-top:5px solid var(--orange);z-index:2}
.brand{left:112px;top:30px;display:flex;align-items:center;gap:14px}
.brand-mark{width:56px;height:56px;border-radius:50%;background:var(--orange)}
.brand-name{font-family:"Montserrat",sans-serif;font-weight:700;font-size:20px;line-height:1.1;color:var(--blue)}
.main-nav{right:112px;top:50px;display:flex;gap:44px;font-family:"Montserrat",sans-serif;font-weight:600;font-size:15px;color:var(--ink)}
.main-nav .active{color:var(--blue)}
.hero-photo{left:0;top:118px;width:1200px;height:640px;
  background:
   radial-gradient(ellipse 170px 200px at 820px 200px,#c9a083 0%,rgba(201,160,131,.55) 45%,rgba(201,160,131,0) 100%),
   radial-gradient(ellipse 300px 260px at 820px 470px,#7f9fb4 0%,rgba(127,159,180,.6) 50%,rgba(127,159,180,0) 100%),
   radial-gradient(ellipse 220px 140px at 560px 500px,#ffffff 0%,rgba(255,255,255,.7) 50%,rgba(255,255,255,0) 100%),
   linear-gradient(100deg,#f7f8f8 0%,#eef1f2 35%,#c9d3d6 62%,#a3b3b8 85%,#8ea0a6 100%)}
.hero-title{left:110px;top:290px;font-family:"Montserrat",sans-serif}
.hero-title .l1{font-size:60px;font-weight:500;color:var(--orange);letter-spacing:2px;line-height:1}
.hero-title .l2{font-size:32px;font-weight:500;color:var(--blue);margin-top:10px;letter-spacing:1px}
.btn{display:inline-block;font-family:"Montserrat",sans-serif;font-weight:700;font-size:16px;border-radius:30px;padding:12px 30px;text-transform:uppercase}
.btn-solid{background:var(--orange);color:#fff}
.btn-line{border:2px solid var(--orange);color:var(--orange);background:#fff;font-size:15px;padding:9px 26px}
.btn-blue{background:var(--blue);color:#fff}
.arrow{display:inline-block;width:14px;height:14px;border-radius:50%;background:currentColor;vertical-align:-1px;margin-left:6px}
.btn-solid .arrow,.btn-blue .arrow{background:#fff}
.badge{width:84px;height:84px;border-radius:50%;background:#fff;border:3px solid var(--blue);z-index:1}
.badge::after{content:"";position:absolute;left:24px;top:24px;width:30px;height:30px;border-radius:50%;background:var(--orange)}
.service-photo{width:350px;height:350px;border-radius:50%;box-shadow:-6px 8px 0 var(--blue)}
.service-title{font-family:"Montserrat",sans-serif;font-weight:500;font-size:42px;color:var(--ink);letter-spacing:1px;line-height:1.25}
.service-text{width:538px;font-size:14px;line-height:28px;color:var(--text)}
.band{left:0;top:2305px;width:1200px;height:500px;
  background:
   radial-gradient(ellipse 260px 160px at 900px 200px,rgba(255,214,150,.55),rgba(255,214,150,0)),
   radial-gradient(ellipse 300px 180px at 250px 300px,rgba(200,110,20,.35),rgba(200,110,20,0)),
   linear-gradient(180deg,#f4a233 0%,var(--orange-deep) 100%)}
.band-title{left:0;top:2380px;width:1200px;text-align:center;font-family:"Montserrat",sans-serif;font-weight:500;font-size:46px;line-height:56px;color:#fff}
.band-text{left:150px;top:2518px;width:900px;text-align:center;font-size:14px;line-height:30px;color:#fff}
.clients-bg{left:0;top:2805px;width:1200px;height:720px;
  background:
   radial-gradient(ellipse 260px 180px at 150px 260px,rgba(190,200,208,.6),rgba(190,200,208,0)),
   radial-gradient(ellipse 300px 200px at 1060px 420px,rgba(190,200,208,.55),rgba(190,200,208,0)),
   linear-gradient(180deg,#f8f9fa,#eceff1)}
.clients-title{left:0;top:2900px;width:1200px;text-align:center;font-family:"Montserrat",sans-serif;font-weight:500;font-size:46px;color:var(--ink);letter-spacing:1px}
.clients-text{left:0;top:2990px;width:1200px;text-align:center;font-size:14px;line-height:28px}
.client{width:136px;height:92px;background:#fff;box-shadow:0 2px 8px rgba(0,0,0,.1);display:flex;flex-direction:column;align-items:center;justify-content:center;gap:4px;font-family:"Open Sans",sans-serif;font-weight:700;font-size:13px;color:var(--blue)}
.client i{width:66px;height:66px;border-radius:50%;display:block}
.client.named i{width:38px;height:38px}
.dots{left:476px;top:3322px;display:flex;gap:8px}
.dots span{width:32px;height:4px;background:#c8c8c8}
.dots .on{background:var(--orange)}
.footer{left:0;top:3520px;width:1200px;height:516px;background:var(--footer)}
.foot-head{font-family:"Montserrat",sans-serif;font-weight:700;font-size:17px;color:#fff;text-decoration:underline;text-decoration-color:var(--orange);text-underline-offset:6px}
.foot-links{list-style:none;font-size:14px;color:#fff;line-height:30px}
.foot-links li::before{content:"»";margin-right:20px}
.contact-row{display:flex;gap:18px;font-size:14px;line-height:27px;color:#fff;margin-bottom:22px}
.contact-row svg{flex:none;margin-top:6px}
.map{left:638px;top:3600px;width:450px;height:284px;
  background:
   radial-gradient(ellipse 60px 140px at 180px 150px,rgba(240,200,90,.55),rgba(240,200,90,0)),
   radial-gradient(ellipse 120px 90px at 360px 80px,rgba(190,220,180,.6),rgba(190,220,180,0)),
   radial-gradient(ellipse 140px 90px at 80px 230px,rgba(200,215,230,.7),rgba(200,215,230,0)),
   linear-gradient(135deg,#f1f1ec,#e4e8ea 60%,#f2ebdb)}
.map-btn{left:652px;top:3614px;background:var(--blue);color:#fff;font-family:"Montserrat",sans-serif;font-weight:700;font-size:13px;padding:8px 14px}
.foot-rule{left:112px;top:3952px;width:976px;height:1px;background:#444}
.copyright{left:112px;top:3980px;font-size:14px;color:#fff}
.social{top:3976px;width:32px;height:32px;border-radius:50%;border:2px solid #fff}
</style>
</head>
<body>

<header class="site-header abs">
  <div class="brand abs"><span class="brand-mark"></span><span class="brand-name">BRIGHTPATH<br>COURSECRAFT</span></div>
  <nav class="main-nav abs"><span class="active">HOME</span><span>PORTFOLIO</span><span>TEAM &amp; EXPERIENCE</span><span>CONTACT US</span></nav>
</header>

<div class="hero-photo abs" role="img" aria-label="Photo of a smiling learner with headphones writing beside a laptop"></div>
<svg class="abs" style="left:0;top:620px" width="1200" height="180" viewBox="0 0 1200 180">
  <path d="M0 30 Q600 230 1200 30 L1200 180 L0 180Z" fill="#fff"/>
  <path d="M0 52 Q600 250 1200 52" fill="none" stroke="#1f6fb5" stroke-width="6"/>
</svg>
<div class="hero-title abs"><div class="l1">BRIGHTPATH</div><div class="l2">COURSECRAFT</div></div>
<a class="btn btn-solid abs" style="left:110px;top:440px">Join us now <span class="arrow"></span></a>
<div class="badge abs" style="left:558px;top:726px"></div>

<div class="service-photo abs" style="left:118px;top:866px;background:radial-gradient(circle at 40% 35%,#6fa0a8 0%,#3f6a74 35%,transparent 60%),radial-gradient(circle at 60% 75%,#d9b8a0 0%,#b99680 40%,transparent 70%),linear-gradient(160deg,#3d5a62,#8a9aa0 55%,#cdb9a6)" role="img" aria-label="Photo of hands typing on a laptop showing an online learning screen"></div>
<h2 class="service-title abs" style="left:555px;top:918px">LIVE TRAINING</h2>
<p class="service-text abs" style="left:557px;top:997px">Lorem ipsum dolor sit amet, consectetur adipiscing elit, sed do eiusmod tempor incididunt ut labore et dolore magna aliqua. Ut enim ad minim veniam, quis nostrud exercitation ullamco laboris nisi ut aliquip ex ea commodo consequat. Duis aute irure dolor in reprehenderit in voluptate velit esse cillum dolore eu fugiat nulla pariatur epteur sint occaecat cupidatat non proident...</p>
<a class="btn btn-line abs" style="left:557px;top:1186px">Read more <span class="arrow"></span></a>

<h2 class="service-title abs" style="left:110px;top:1342px">E-LEARNING<br>DEVELOPMENT</h2>
<p class="service-text abs" style="left:110px;top:1470px">Lorem ipsum dolor sit amet, consectetur adipiscing elit, sed do eiusmod tempor incididunt ut labore et dolore magna aliqua. Ut enim ad minim veniam, quis nostrud exercitation ullamco laboris nisi ut aliquip ex ea commodo consequat. Duis aute irure dolor in reprehenderit in voluptate velit esse cillum dolore eu fugiat nulla pariatur epteur sint occaecat cupidatat non proident...</p>
<a class="btn btn-line abs" style="left:110px;top:1658px">Read more <span class="arrow"></span></a>
<div class="service-photo abs" style="left:736px;top:1336px;background:radial-gradient(circle at 35% 45%,#a9c9a0 0%,rgba(169,201,160,0) 22%),radial-gradient(circle at 70% 60%,#8c9ca3 0%,rgba(140,156,163,0) 35%),linear-gradient(160deg,#f3f6f6,#d5dee0 55%,#9fb0b5)" role="img" aria-label="Photo of a person working at a bright desk with a laptop"></div>

<div class="service-photo abs" style="left:118px;top:1810px;background:radial-gradient(circle at 30% 35%,#2f5f92 0%,rgba(47,95,146,0) 35%),radial-gradient(circle at 72% 40%,#6e8fb0 0%,rgba(110,143,176,0) 35%),radial-gradient(circle at 60% 80%,#c8ccd0 0%,rgba(200,204,208,0) 40%),linear-gradient(160deg,#14223a,#2b4466 50%,#8a98a4)" role="img" aria-label="Photo of a developer pointing at code on dual monitors"></div>
<h2 class="service-title abs" style="left:555px;top:1862px">WEB APP DEVELOPMENT</h2>
<p class="service-text abs" style="left:557px;top:1942px">Lorem ipsum dolor sit amet, consectetur adipiscing elit, sed do eiusmod tempor incididunt ut labore et dolore magna aliqua. Ut enim ad minim veniam, quis nostrud exercitation ullamco laboris nisi ut aliquip ex ea commodo consequat. Duis aute irure dolor in reprehenderit in voluptate velit esse cillum dolore eu fugiat nulla pariatur epteur sint occaecat cupidatat non proident...</p>
<a class="btn btn-line abs" style="left:557px;top:2130px">Read more <span class="arrow"></span></a>

<div class="band abs" role="img" aria-label="Orange-tinted photo of a workspace with laptop"></div>
<div class="clients-bg abs" role="img" aria-label="Faded photo of laptops on a desk"></div>
<svg class="abs" style="left:0;top:2640px" width="1200" height="200" viewBox="0 0 1200 200">
  <path d="M0 0 L1200 0 L1200 60 Q600 230 0 60Z" fill="#e8871a"/>
  <path d="M0 76 Q600 250 1200 76" fill="none" stroke="#1f6fb5" stroke-width="6"/>
</svg>
<h2 class="band-title abs">Instructional Design &amp; Courseware<br>Development Firm</h2>
<p class="band-text abs">Brightpath Coursecraft is a HUBZone Certified, SBA 8(a) Certified, Native American Owned Small Disadvantaged Business located in Denver, Colorado. We have designed and delivered SCORM compliant eLearning, webinar, web-based training (WBT), instructor-led training (ILT), virtual ILT (VILT), blended, and 3D immersive training courses.</p>
<a class="btn btn-blue abs" style="left:502px;top:2644px">Join us today <span class="arrow"></span></a>
<div class="badge abs" style="left:558px;top:2748px"></div>

<h2 class="clients-title abs">OUR CLIENTS</h2>
<p class="clients-text abs">We offer a bench of 60+ UX and UI designers, Product Owners, Scrum Masters, full stack developers<br>and more working together to build genuinely useful applications.</p>
<div class="client abs" style="left:144px;top:3068px"><i style="background:#5a78b0"></i></div>
<div class="client abs" style="left:306px;top:3068px"><i style="background:#c9a44a"></i></div>
<div class="client abs" style="left:468px;top:3068px"><i style="background:#7a2a2a"></i></div>
<div class="client named abs" style="left:630px;top:3068px"><i style="background:#3a9a5a"></i>Ventrelle</div>
<div class="client abs" style="left:792px;top:3068px"><i style="background:#2c3e66"></i></div>
<div class="client abs" style="left:954px;top:3068px"><i style="background:#c25a5a"></i></div>
<div class="client abs" style="left:144px;top:3182px"><i style="background:#3d5ea8"></i></div>
<div class="client named abs" style="left:306px;top:3182px"><i style="background:#c8102e"></i>Kestrel State</div>
<div class="client abs" style="left:468px;top:3182px"><i style="background:#b8862a"></i></div>
<div class="client abs" style="left:630px;top:3182px"><i style="background:#8a8f96"></i></div>
<div class="client named abs" style="left:792px;top:3182px"><i style="background:#1f4e9a"></i>Skyline Corps</div>
<div class="client named abs" style="left:954px;top:3182px"><i style="background:#c0392b"></i>Ridgefire</div>
<div class="dots abs"><span></span><span></span><span class="on"></span><span></span><span></span></div>

<div class="footer abs"></div>
<svg class="abs" style="left:0;top:3400px" width="1200" height="130" viewBox="0 0 1200 130">
  <path d="M0 130 L0 110 Q600 -30 1200 110 L1200 130Z" fill="#1e1e1e"/>
  <path d="M0 98 Q600 -44 1200 98" fill="none" stroke="#1f6fb5" stroke-width="6"/>
</svg>
<div class="badge abs" style="left:558px;top:3410px"></div>

<h3 class="foot-head abs" style="left:112px;top:3606px">QUICK LINKS</h3>
<ul class="foot-links abs" style="left:114px;top:3650px">
  <li>Home</li><li>About Us</li><li>Portfolio</li><li>Team &amp; Experience</li><li>Latest News</li><li>Help</li><li>Privacy policy</li><li>Contact Us</li>
</ul>

<h3 class="foot-head abs" style="left:328px;top:3606px">CONTACT US</h3>
<div class="abs" style="left:330px;top:3650px;width:300px">
  <div class="contact-row"><svg width="14" height="18" viewBox="0 0 14 18"><path d="M7 1a6 6 0 0 1 6 6c0 4-6 10-6 10S1 11 1 7a6 6 0 0 1 6-6z" fill="none" stroke="#fff" stroke-width="1.6"/><circle cx="7" cy="7" r="2" fill="#fff"/></svg><span>5820 E Larkspur Avenue, Suite 2-140<br>Aurora, CO. 80012.</span></div>
  <div class="contact-row"><svg width="14" height="18" viewBox="0 0 14 18"><path d="M7 1a6 6 0 0 1 6 6c0 4-6 10-6 10S1 11 1 7a6 6 0 0 1 6-6z" fill="none" stroke="#fff" stroke-width="1.6"/><circle cx="7" cy="7" r="2" fill="#fff"/></svg><span>Velmoro Plaza, Street 62 Sur, 14-87.<br>Medellín, Antioquia.</span></div>
  <div class="contact-row"><svg width="14" height="14" viewBox="0 0 14 14"><path d="M3 1l2 3-1.5 1.5a8 8 0 0 0 5 5L10 9l3 2-1 2C6 13 1 8 1 2z" fill="#fff"/></svg><span>+1 555 014 7730</span></div>
  <div class="contact-row" style="font-size:13px"><svg width="16" height="12" viewBox="0 0 16 12"><rect x="1" y="1" width="14" height="10" fill="none" stroke="#fff" stroke-width="1.4"/><path d="M1 1l7 6 7-6" fill="none" stroke="#fff" stroke-width="1.4"/></svg><span>support@brightpathcoursecraft.example</span></div>
</div>

<div class="map abs" role="img" aria-label="Street map showing the office locations"></div>
<div class="map-btn abs">GET A DIRECTION ➜</div>

<div class="foot-rule abs"></div>
<p class="copyright abs">© Copyright 2019 Brightpath Coursecraft. All Rights Reserved.</p>
<span class="social abs" style="left:964px" aria-label="Social profile"></span>
<span class="social abs" style="left:1007px" aria-label="Social profile"></span>
<span class="social abs" style="left:1050px" aria-label="Social profile"></span>

</body>
</html>
```